Design a modern, classy & professional business card for an online real estate agency, specializing in medium-luxury properties in Thailand and later in Singapore and UK.

Possible design ideas so far: (not essential)

- curved corner(s) to the card, white on front & turquoise on back or visa versa.

- front of card - clear and simple, company name in metallic grey/monochrome, logo graphic & company name on front in spot UV or embossed/debossed effect.

- back of card - large, close-cropped, 'ghost' patterns of the C-shaped curves of logo, or company name repeated on back of card in spot UV.

Target Market(s)

- young to middle-aged professionals mainly (but ideally should design should suit all)

- UK, US,EU,AUS & ASIAN mainly (but ideally should design should suit all countries)

Industry/Entity Type

Real Estate

Requirements
Must have
• THEME:
- Luxurious & Modern
- Clean & striking
- Unique & creative

INFO:
- Logo & company name on front
- Contact details on back:

Tobias Hennlund
Managing Director

www.velmontestates.asia
www.velmontestates.co.uk

Tel: 083-274-6159
email: tobias@velmontestates.asia

(contact details can be displayed in any order as suites design.)

Nice to have
• - curved corner(s) to the card, white on front & turquoise on back or visa versa.

Should not have
• - No generic images of properties, palm trees/coconut trees etc.

- No other other bold colors, except for main turquoise, grey, metallic white & black theme.

- No obvious business card templates

```html
<!DOCTYPE html>
<html lang="en">
<head>
<meta charset="utf-8">
<title>Velmont Estates – Business Card</title>
<link rel="stylesheet" href="https://fonts.googleapis.com/css2?family=Open+Sans:wght@400;600;700&display=swap">
<style>
  :root {
    --bg: #e9e7e4;
    --teal: #2fb3ad;
    --teal-deep: #249e98;
    --teal-light: #5fd0ca;
    --card-white: #ffffff;
    --card-shade: #f1f1f1;
    --ink: #4a4a4a;
    --ink-soft: #6b6b6b;
  }
  * { box-sizing: border-box; margin: 0; padding: 0; }
  html, body {
    width: 1200px;
    height: 840px;
    overflow: hidden;
    background: var(--bg);
    font-family: "Open Sans", Arial, sans-serif;
  }
  .canvas {
    position: relative;
    width: 1200px;
    height: 840px;
  }
  .card {
    position: absolute;
    border-radius: 22px;
    box-shadow: 0 10px 28px rgba(0,0,0,0.18);
    overflow: hidden;
  }
  .card--pattern {
    left: 90px;
    top: 260px;
    width: 560px;
    height: 320px;
    background: linear-gradient(135deg, var(--teal-light) 0%, var(--teal) 45%, var(--teal-deep) 100%);
  }
  .card--contact {
    left: 760px;
    top: 140px;
    width: 340px;
    height: 560px;
    background: linear-gradient(180deg, var(--card-white) 55%, var(--card-shade) 100%);
    display: flex;
    flex-direction: column;
    align-items: center;
    padding-top: 150px;
    text-align: center;
    color: var(--ink);
  }
  .brand {
    display: flex;
    align-items: center;
    gap: 12px;
    margin-bottom: 34px;
  }
  .brand__mark {
    width: 40px;
    height: 40px;
    background: var(--teal);
  }
  .brand__name {
    font-size: 26px;
    font-weight: 400;
    color: var(--ink-soft);
    letter-spacing: 0.5px;
  }
  .person__name {
    font-size: 20px;
    font-weight: 700;
    color: var(--ink);
  }
  .person__role {
    font-size: 14px;
    color: var(--ink-soft);
    margin-top: 2px;
  }
  .divider {
    width: 120px;
    height: 2px;
    background: var(--teal);
    margin: 18px 0 18px;
  }
  .contact-list {
    list-style: none;
    font-size: 13px;
    line-height: 1.7;
    color: var(--ink-soft);
  }
  .contact-list .gap { margin-top: 12px; }
</style>
</head>
<body>
  <main class="canvas">
    <section class="card card--pattern" role="img" aria-label="Turquoise card back with a ghosted spot-UV pattern of interlocking C-shaped rings"></section>

    <section class="card card--contact">
      <div class="brand">
        <span class="brand__mark"></span>
        <span class="brand__name">Velmont Estates</span>
      </div>
      <h1 class="person__name">Tobias Hennlund</h1>
      <p class="person__role">Managing Director</p>
      <div class="divider"></div>
      <ul class="contact-list">
        <li>083-274-6159</li>
        <li>tobias@velmontestates.asia</li>
        <li class="gap">www.velmontestates.asia</li>
        <li>www.velmontestates.co.uk</li>
      </ul>
    </section>
  </main>
</body>
</html>
```